Popup Nightclub Grand Opening Flyer

We need to design a flyer for the grand opening of an upscale, exclusive nightclub called "Lantern". The design needs to be chic and exclusive. The background should be black and the text should primarily be white. We like minimalist designs.

Here is the text for the flyer
-
Velvetroll Atlanta Presents

Lantern (LOGO)

A Popup Nightclub Experience
For one night Only

Friday, October 18, 2013
Party begins at 9PM

INVITE ONLY

See invitation for location details
(Velvetroll Atlanta logo)

-
Examples we like

http://cdn4-x.pressfolio-example.com/sites/default/files/styles/image_content_width/hash/3b/fd/2468013579_4421_flyer.jpg?itok=K9rtQw2z

http://files.hubspace-example.net/files/8Hqq-Tr72WWE3kaRbTmcxP5QZK2F396J8nbRw4CKMHfdX2Y7qSEF-MqjxDoNrLY3QCyQJD7npjGaRq3k-Mhx6hqf3MDSWf8r3/2zenSaturdays.jpg

http://morvex-example.com/wp-content/uploads/siteskin/widgetkit/gallery/2zen/2zen-gen_qstay4-01.jpg

Hi All, one thing that we are seeing that we don't like is on over emphasis on the phrase "a popup nightclub experience" please don't make this the largest thing on the flyer

Target Market(s)

Target market is 25-35 year olds who are affluent (rich) and like luxury brands

Requirements
Must have
• Dark Background
Nice to have
• Velvetroll Logo on the bottom
Modern text that isn't curvy
Should not have
• Curved text

```html
<!DOCTYPE html>
<html lang="en">
<head>
<meta charset="utf-8">
<title>Lantern Nightclub – Popup Opening</title>
<link rel="stylesheet" href="https://fonts.googleapis.com/css2?family=Montserrat:wght@300;600;700&display=swap">
<style>
  :root {
    --bg-deep: #050505;
    --bg-mid: #1c1c1c;
    --text-main: #ffffff;
    --text-muted: #a3a3a3;
    --accent: #e9d400;
    --accent-glow: rgba(233, 212, 0, 0.55);
    --rule: #d8d8d8;
    --emblem-light: #5a5a5a;
    --emblem-dark: #141414;
  }
  * { margin: 0; padding: 0; box-sizing: border-box; }
  html, body {
    width: 787px;
    height: 1200px;
    overflow: hidden;
    background: var(--bg-deep);
  }
  .flyer {
    position: relative;
    width: 787px;
    height: 1200px;
    overflow: hidden;
    font-family: "Montserrat", Arial, sans-serif;
    color: var(--text-main);
    text-align: center;
  }
  .backdrop {
    position: absolute;
    inset: 0;
    background:
      radial-gradient(ellipse at 50% 35%, var(--bg-mid) 0%, var(--bg-deep) 70%),
      var(--bg-deep);
  }
  .line {
    position: absolute;
    left: 0;
    width: 100%;
    text-transform: uppercase;
    white-space: nowrap;
  }
  .presenter {
    top: 14px;
    font-size: 28px;
    font-weight: 700;
    color: var(--text-muted);
    letter-spacing: 0.5px;
  }
  .emblem {
    position: absolute;
    left: 189px;
    top: 190px;
    width: 410px;
    height: 410px;
    border-radius: 50%;
    background: radial-gradient(circle at 40% 35%, var(--emblem-light) 0%, var(--emblem-dark) 75%);
  }
  .venue-name {
    top: 640px;
    font-size: 70px;
    font-weight: 300;
    letter-spacing: 14px;
    padding-left: 14px;
  }
  .venue-type {
    top: 718px;
    font-size: 44px;
    font-weight: 300;
    letter-spacing: 7px;
    padding-left: 7px;
  }
  .tagline {
    top: 788px;
    font-size: 41px;
    font-weight: 700;
  }
  .divider {
    position: absolute;
    left: 100px;
    top: 846px;
    width: 587px;
    height: 2px;
    background: var(--rule);
  }
  .highlight {
    top: 854px;
    font-size: 64px;
    font-weight: 700;
    color: var(--accent);
    text-shadow: 0 0 14px var(--accent-glow), 0 0 30px var(--accent-glow);
  }
  .date {
    top: 938px;
    font-size: 33px;
    font-weight: 700;
    letter-spacing: 2px;
  }
  .access {
    top: 1010px;
    font-size: 34px;
    font-weight: 700;
  }
  .location-note {
    top: 1062px;
    font-size: 15px;
    font-weight: 700;
  }
  .host-mark {
    position: absolute;
    left: 0;
    top: 1110px;
    width: 100%;
    display: flex;
    justify-content: center;
    align-items: center;
    gap: 18px;
  }
  .host-mark .dot {
    width: 46px;
    height: 46px;
    border-radius: 50%;
    background: var(--text-main);
  }
  .host-mark .name {
    font-size: 34px;
    font-weight: 300;
    letter-spacing: 3px;
    text-transform: uppercase;
    color: var(--text-main);
  }
</style>
</head>
<body>
  <main class="flyer">
    <div class="backdrop" role="img" aria-label="Black background with fine diagonal grey stripes curving near the bottom"></div>

    <p class="line presenter">Velvetroll Atlanta Presents</p>

    <div class="emblem" role="img" aria-label="Lantern nightclub emblem"></div>
    <h1 class="line venue-name">Lantern</h1>
    <p class="line venue-type">Nightclub</p>

    <p class="line tagline">A Popup Nightclub Experience</p>
    <div class="divider"></div>
    <p class="line highlight">For One Night Only</p>
    <p class="line date">Friday October 18 2013 @ 9:00PM</p>

    <p class="line access">Invite Only</p>
    <p class="line location-note">See invitation for location details</p>

    <div class="host-mark">
      <span class="dot"></span>
      <span class="name">Velvetroll Atlanta</span>
    </div>
  </main>
</body>
</html>
```